Veldmark Supplies Business Card

Professional business card that stand out to our potential customers. Front and back with clean modern design

Industry/Entity Type

Oil and gas

Contact Information for Business Card

Name, address, website , office phone and cell number

Requirements
Must have
• Editable files for each employee

```html
<!DOCTYPE html>
<html lang="en">
<head>
<meta charset="utf-8">
<title>Veldmark Supplies Business Card</title>
<link href="https://fonts.googleapis.com/css2?family=Archivo:wght@400;700;800&display=swap" rel="stylesheet">
<style>
  :root {
    --backdrop: #3c3c3c;
    --card-dark: #2a2a2a;
    --card-darker: #232323;
    --brand-red: #ff0000;
    --white: #ffffff;
    --steel: #9a9a9a;
    --emboss: #1c1c1c;
  }
  * { box-sizing: border-box; margin: 0; padding: 0; }
  html, body {
    width: 1200px; height: 803px; overflow: hidden;
    background: var(--backdrop);
    font-family: "Archivo", Arial, sans-serif;
  }
  .stage {
    position: relative; width: 1200px; height: 803px;
    display: flex; align-items: center; justify-content: center; gap: 50px;
  }
  .card {
    position: relative; width: 530px; height: 304px;
    border-radius: 20px; overflow: hidden;
    background: var(--card-dark);
    box-shadow: 0 18px 40px rgba(0,0,0,.35);
  }
  /* Front */
  .card-front .red-field {
    position: absolute; inset: 0;
    background: var(--brand-red);
    clip-path: polygon(0 0, 60% 0, 72% 100%, 0 100%);
  }
  .card-front .mark-zone {
    position: absolute; top: 0; right: 0; width: 40%; height: 100%;
    display: flex; align-items: center; justify-content: center;
    padding-left: 40px;
  }
  .mark-name {
    font-weight: 800; font-size: 22px; line-height: 1.1;
    color: var(--steel); text-transform: uppercase; letter-spacing: 1px;
    text-align: center;
  }
  .front-content {
    position: absolute; left: 34px; top: 30px; color: var(--white);
  }
  .wordmark {
    display: flex; align-items: center; gap: 8px;
    font-weight: 800; font-size: 15px; letter-spacing: 1.5px;
    text-transform: uppercase; color: var(--white);
  }
  .wordmark .square { width: 12px; height: 12px; background: var(--white); }
  .person-name {
    margin-top: 26px; font-weight: 700; font-size: 24px;
    text-transform: uppercase; letter-spacing: .5px;
  }
  .person-title { font-size: 12px; margin-top: 2px; }
  .address { margin-top: 18px; font-size: 12.5px; line-height: 1.35; }
  .contact-list { list-style: none; margin-top: 12px; font-size: 12.5px; line-height: 1.45; }
  .contact-list li { display: flex; align-items: center; gap: 8px; }
  .contact-list svg { width: 11px; height: 11px; flex: none; }
  /* Back */
  .card-back {
    background: linear-gradient(135deg, var(--card-dark), var(--card-darker));
    display: flex; align-items: center; justify-content: center;
  }
  .back-name {
    font-weight: 800; font-size: 30px; letter-spacing: 2px;
    text-transform: uppercase; color: var(--emboss);
  }
</style>
</head>
<body>
<main class="stage">
  <section class="card card-front" aria-label="Business card front">
    <div class="red-field"></div>
    <div class="mark-zone">
      <p class="mark-name">Veldmark<br>Supplies</p>
    </div>
    <div class="front-content">
      <div class="wordmark"><span class="square"></span>Veldmark Supplies</div>
      <h1 class="person-name">Daniel Reyes</h1>
      <p class="person-title">President</p>
      <p class="address">4120 Cedar Ridge Road<br>Halden, Canada 20481</p>
      <ul class="contact-list">
        <li>
          <svg viewBox="0 0 12 12" aria-hidden="true"><path fill="#fff" d="M2.5 1l2 2-1 1.5c.7 1.4 1.6 2.3 3 3L8 6.5l2 2-1.2 1.8C5.5 10 2 6.5 1 3.3z"/></svg>
          555-201-4478
        </li>
        <li>
          <svg viewBox="0 0 12 12" aria-hidden="true"><rect x="3" y="1" width="6" height="10" rx="1" fill="none" stroke="#fff" stroke-width="1.2"/></svg>
          555-309-6612
        </li>
        <li>
          <svg viewBox="0 0 12 12" aria-hidden="true"><rect x="1" y="2.5" width="10" height="7" fill="#fff"/><path d="M1 2.5l5 4 5-4" fill="none" stroke="#ff0000" stroke-width="1"/></svg>
          info@veldmarksupplies.com
        </li>
        <li>
          <svg viewBox="0 0 12 12" aria-hidden="true"><circle cx="6" cy="6" r="5" fill="#fff"/><path d="M1 6h10M6 1c-2 2.5-2 7.5 0 10M6 1c2 2.5 2 7.5 0 10" fill="none" stroke="#ff0000" stroke-width=".8"/></svg>
          www.veldmarksupplies.com
        </li>
      </ul>
    </div>
  </section>

  <section class="card card-back" aria-label="Business card back">
    <p class="back-name">Veldmark Supplies</p>
  </section>
</main>
</body>
</html>
```